The Vantor Codex Book Cover

"The Vantor Codex" is a book I wrote with the slogan "Unlock Performance, Spark Engagement: Master the Art of Building Winning Cultures in Today's Hybrid World". The book is designed around a methodology that's mine and that I attached. I would love to see the graphic of the methodology integrated in the design in a very subtle way. Use colors from the model but the book cover should be catchy, modern and engaging to the eye.
Overall the book is about three key elements towards success:
- (Self) Directions (purpose)
- Human experience (people and psychological safety)
- Maximize engagement
The methodology is a FLOW so flow is something that could be incorporated as well in the concept.
Low design quality
Managers and Teams

```html
<!DOCTYPE html>
<html lang="en">
<head>
<meta charset="utf-8">
<title>The Vantor Codex — Book Cover</title>
<link href="https://fonts.googleapis.com/css2?family=Bebas+Neue&family=Cinzel:wght@400&family=Oswald:wght@500&display=swap" rel="stylesheet">
<style>
  :root {
    --ink: #000000;
    --paper: #ffffff;
    --flow-magenta: #e21ee0;
    --flow-amber: #e7a23c;
    --flow-green: #8fe03a;
    --flow-blue: #2f5d9a;
    --flow-ice: #cfe6ff;
  }
  html, body {
    margin: 0;
    padding: 0;
    width: 934px;
    height: 1200px;
    overflow: hidden;
    background: var(--ink);
  }
  .cover {
    position: relative;
    width: 934px;
    height: 1200px;
    background: var(--ink);
    color: var(--paper);
    text-align: center;
  }
  .author {
    position: absolute;
    top: 64px;
    left: 0;
    width: 100%;
    margin: 0;
    font-family: "Cinzel", serif;
    font-weight: 400;
    font-size: 57px;
    letter-spacing: 1px;
    line-height: 1;
  }
  .title {
    position: absolute;
    top: 200px;
    left: 0;
    width: 100%;
    margin: 0;
    font-family: "Bebas Neue", sans-serif;
    font-weight: 400;
    line-height: 1;
  }
  .title-lead {
    display: block;
    font-size: 84px;
    letter-spacing: 0;
  }
  .title-main {
    display: block;
    margin-top: 3px;
    font-size: 148px;
    letter-spacing: 1px;
  }
  .tagline {
    position: absolute;
    top: 414px;
    left: 220px;
    width: 485px;
    height: 38px;
    border-top: 3px solid var(--paper);
    border-bottom: 3px solid var(--paper);
    box-sizing: border-box;
    margin: 0;
    font-family: "Oswald", sans-serif;
    font-weight: 500;
    font-size: 13px;
    letter-spacing: 8.2px;
    line-height: 32px;
    text-transform: uppercase;
    white-space: nowrap;
  }
  .subtitle {
    position: absolute;
    top: 466px;
    left: 0;
    width: 100%;
    margin: 0;
    font-family: "Cinzel", serif;
    font-size: 17px;
    line-height: 21px;
    letter-spacing: 0.3px;
  }
  .flow-art {
    position: absolute;
    top: 572px;
    left: 190px;
    width: 592px;
    height: 460px;
    background:
      radial-gradient(ellipse 22% 38% at 18% 38%, rgba(226,30,224,0.75), transparent 70%),
      radial-gradient(ellipse 20% 22% at 20% 80%, rgba(231,162,60,0.7), transparent 70%),
      radial-gradient(ellipse 14% 14% at 53% 52%, rgba(207,230,255,0.8), transparent 70%),
      radial-gradient(ellipse 28% 30% at 72% 30%, rgba(143,224,58,0.45), transparent 70%),
      radial-gradient(ellipse 30% 28% at 75% 72%, rgba(47,93,154,0.7), transparent 70%);
    filter: blur(6px);
  }
  .editor {
    position: absolute;
    top: 1093px;
    left: 0;
    width: 100%;
    margin: 0;
    font-family: "Cinzel", serif;
    font-weight: 400;
    font-size: 57px;
    letter-spacing: 1px;
    line-height: 1;
  }
</style>
</head>
<body>
  <main class="cover">
    <p class="author">AUTHOR NAME</p>
    <h1 class="title">
      <span class="title-lead">THE VANTOR</span>
      <span class="title-main">CODEX</span>
    </h1>
    <p class="tagline">Unlock Performance, Spark Engagement:</p>
    <p class="subtitle">Master the Art of Building Winning Cultures<br>in Today's Hybrid World</p>
    <div class="flow-art" role="img" aria-label="Glowing light-trail infinity loop in magenta, amber, green and blue, symbolising the flow methodology"></div>
    <p class="editor">EDITOR</p>
  </main>
</body>
</html>
```